Hemp company needs website/online store

We are a startup hemp company and we need an online storefront designed. We are very open do design, but will include our logo to help. We make 100% hemp derived products like edibles, concentrates, vapes and THCA flower. Everything is grown locally, and all products are extracted and made in house.

• I would like to highlight that we have Cannabis products that are hemp derived and 100% legal across the US. Also that all cannabis is locally grown and products are extracted and made in house and sent out for third party lab testing.

```html
<!DOCTYPE html>
<html lang="en">
<head>
<meta charset="utf-8">
<title>Sunnyfield Hemp</title>
<link href="https://fonts.googleapis.com/css2?family=Baloo+2:wght@500;600;700&family=Lato:wght@400;700&display=swap" rel="stylesheet">
<style>
:root{
  --lime:#9dbb3a;
  --green:#4c8432;
  --deep:#3c6e28;
  --footer:#4d8733;
  --cream:#fbfdeb;
  --grey:#f2f2f2;
  --ink:#333;
  --muted:#555;
  --star:#f2a41c;
}
*{box-sizing:border-box;margin:0;padding:0}
html,body{width:1200px;height:3934px;overflow:hidden}
body{position:relative;font-family:'Lato',sans-serif;color:var(--ink);background:#fff}
.abs{position:absolute}
h1,h2,h3,.display{font-family:'Baloo 2',sans-serif}
.btn{position:absolute;display:flex;align-items:center;justify-content:center;font-family:'Baloo 2',sans-serif;font-weight:600}
.btn-grad{background:linear-gradient(90deg,var(--lime),var(--green));color:#fff;box-shadow:3px 4px 6px rgba(0,0,0,.25)}

/* header */
.topbar{left:435px;top:0;width:765px;height:50px;background:linear-gradient(90deg,var(--lime),var(--green));clip-path:polygon(0 0,100% 0,100% 100%,30px 100%);color:#fff;font-size:14px}
.topbar span{position:absolute;top:16px}
.topbar .sq{width:24px;height:24px;border:1.5px solid #fff;top:12px}
.brand{left:110px;top:20px;width:160px;height:90px;text-align:center}
.brand .dot{width:34px;height:34px;border-radius:50%;background:var(--green);margin:0 auto}
.brand .name{font-family:'Baloo 2',sans-serif;font-weight:700;font-size:30px;color:var(--green);line-height:1.3}
.nav{top:72px;font-size:16px;color:#222}
.nav.active{color:var(--green);text-decoration:underline}
.nav-cta{left:978px;top:66px;width:110px;height:40px;background:var(--lime);color:#fff;font-size:16px;box-shadow:3px 3px 0 var(--green)}

/* hero */
.hero{left:0;top:119px;width:1200px;height:662px}
.hero-side{left:40px;width:12px;height:12px;border-radius:50%;background:#fff}
.hero-copy{left:0;width:1200px;text-align:center;color:#fff}

/* about */
.about-art{left:76px;top:870px;width:390px;height:344px;border-radius:6px;background:linear-gradient(150deg,#a9c86a,#5e9238 55%,#3a6a26)}
.about-title{left:537px;top:885px;font-size:38px;font-weight:600;color:var(--deep)}
.accent{color:var(--lime)}
.about-text{left:537px;top:944px;width:555px;font-size:14.5px;line-height:28px;color:#444}
.about-text p+p{margin-top:28px}

/* products */
.products{left:0;top:1313px;width:1200px;height:728px;background:var(--cream)}
.sec-title{left:0;width:1200px;text-align:center;font-size:42px;font-weight:600;color:var(--deep)}
.sec-sub{left:230px;width:740px;text-align:center;font-size:15px;line-height:26px;color:#444}
.card{top:1509px;width:289px;height:450px;background:#fff;border-radius:10px;box-shadow:0 4px 14px rgba(0,0,0,.1);border-bottom:7px solid var(--lime);text-align:center}
.card.mid{border-bottom-color:var(--green)}
.card .ph{margin:0 auto;width:272px;height:268px;border-radius:8px}
.card h3{font-size:19px;font-weight:600;color:#222;margin-top:22px}
.card p{font-size:13.5px;line-height:24px;color:#555;width:230px;margin:8px auto 0}
.card .buy{position:relative;display:inline-flex;margin-top:18px;width:103px;height:36px;align-items:center;justify-content:center;background:var(--lime);color:#222;font-family:'Baloo 2',sans-serif;font-weight:600;font-size:14px}
.card.mid .buy{background:var(--green);color:#fff}
.arrow{width:34px;height:34px;border-radius:50%;background:var(--green)}

/* touch */
.touch{left:0;top:2041px;width:1200px;height:448px;background:radial-gradient(ellipse at 30% 40%,#9cc23f,#6f9f33 50%,#4e8330)}
.touch-text{left:150px;width:900px;text-align:center;color:#fff;font-weight:700;font-size:15px;line-height:29px}

/* reviews */
.review{width:310px;background:#fff;border:1px solid #ddd;box-shadow:0 3px 10px rgba(0,0,0,.08);padding:30px 20px 0 18px}
.review .stars{color:var(--star);font-size:22px;letter-spacing:1px}
.review p{margin-top:14px;font-size:15px;line-height:27.5px;color:#333}
.who{display:flex;align-items:center;margin-top:16px}
.avatar{width:64px;height:64px;border-radius:50%;background:linear-gradient(#c9b8a3,#7a6b5a);border:2px solid #ddd;flex:none}
.who b{display:block;font-family:'Baloo 2',sans-serif;font-size:15px;font-weight:700;color:#222;margin-left:12px}
.who small{display:block;font-size:12px;font-weight:700;color:#999;margin-left:12px}

/* contact */
.contact{left:0;top:3088px;width:1200px;height:442px;background:var(--grey)}
.field{left:111px;width:332px;height:49px;background:#fff;font-size:13.5px;color:#555;padding:16px 0 0 17px}
.info-ic{left:813px;width:62px;height:62px;border-radius:50%;background:linear-gradient(135deg,var(--lime),var(--green));box-shadow:0 3px 6px rgba(0,0,0,.2)}
.info-txt{left:890px;font-size:15px;line-height:28px;color:#444}
.info-txt b{font-family:'Baloo 2',sans-serif;font-size:15px;letter-spacing:.5px;color:#222}

/* footer */
.footer{left:0;top:3530px;width:1200px;height:404px;background:var(--footer);color:#fff}
.f-title{top:88px;font-family:'Baloo 2',sans-serif;font-weight:600;font-size:20px}
.f-list{top:124px;list-style:none;font-size:14.5px;line-height:34.5px}
.f-list li::before{content:"➜ ";font-size:12px}
.f-ic{left:110px;width:30px;height:30px;border-radius:50%;background:#fff}
.f-social{top:239px;width:32px;height:32px;border-radius:50%;background:#fff}
</style>
</head>
<body>

<!-- header -->
<div class="abs topbar">
  <span style="left:44px">&#9742;&nbsp; Call : +1 555 010 2040</span>
  <span style="left:256px">&#9993;&nbsp;&nbsp; Email : info@sunnyfieldhemp.com</span>
  <span class="sq" style="left:540px"></span>
  <span class="sq" style="left:584px"></span>
  <span class="sq" style="left:628px"></span>
</div>
<div class="abs brand"><div class="dot"></div><div class="name">Sunnyfield</div></div>
<div class="abs nav active" style="left:401px">Home</div>
<div class="abs nav" style="left:515px">About Us</div>
<div class="abs nav" style="left:640px">Services</div>
<div class="abs nav" style="left:757px">Testimonials</div>
<div class="abs nav" style="left:907px">Blog</div>
<div class="btn nav-cta">Contact Us</div>

<!-- hero -->
<svg class="abs hero" viewBox="0 0 1200 662" role="img" aria-label="Greenhouse full of rows of potted hemp plants">
  <defs>
    <linearGradient id="heroPhoto" x1="0" y1="0" x2="0" y2="1">
      <stop offset="0" stop-color="#7d8a80"/><stop offset=".35" stop-color="#3f5a34"/><stop offset="1" stop-color="#2e4a22"/>
    </linearGradient>
    <linearGradient id="swoosh" x1="0" x2="1"><stop offset="0" stop-color="#5f9232"/><stop offset=".5" stop-color="#a9c43c"/><stop offset="1" stop-color="#5f9232"/></linearGradient>
  </defs>
  <path d="M190 520 Q600 760 1010 520 Q600 710 190 520Z" fill="url(#swoosh)"/>
  <path d="M0 0 H1200 V400 Q600 820 0 400Z" fill="url(#heroPhoto)"/>
</svg>
<div class="abs hero-side" style="top:220px"></div>
<div class="abs hero-side" style="top:261px"></div>
<div class="abs hero-side" style="top:298px"></div>
<div class="abs hero-side" style="top:334px"></div>
<div class="abs hero-copy display" style="top:175px;font-size:30px;font-weight:500">Welcome to</div>
<h1 class="abs hero-copy" style="top:212px;font-size:72px;font-weight:700">Sunnyfield Hemp</h1>
<div class="abs hero-copy" style="top:312px;font-size:15px;font-weight:700;line-height:29px">we have Cannabis products that are hemp derived and 100% legal across the US. Also that all cannabis is locally<br>grown and products are extracted and made in house and sent out for third party lab testing.</div>
<div class="btn" style="left:524px;top:391px;width:153px;height:49px;background:#fff;color:var(--green);font-size:19px">Get Started</div>

<!-- about -->
<div class="abs about-art" role="img" aria-label="Hemp leaf illustration inside a square frame"></div>
<h2 class="abs about-title">About Sunnyfield <span class="accent">Hemp</span></h2>
<div class="abs about-text">
  <p>Nam libero tempore, cum soluta nobis est eligendi optio cumque nihil impedit quo minus id quod maxime placeat facere possimus, omnis voluptas assumenda est, omnis dolor repellendus.</p>
  <p>Temporibus autem quibusdam et aut officiis debitis aut rerum necessitatibus saepe eveniet ut et voluptates repudiandae sint et molestiae non recusandae. Itaque earum rerum hic tenetur a sapiente delectus, ut aut reiciendis voluptatibus maiores alias consequatur aut perferendis doloribus asperiores repellat.</p>
</div>
<div class="btn btn-grad" style="left:537px;top:1186px;width:152px;height:51px;font-size:19px">Read More</div>

<!-- products -->
<div class="abs products"></div>
<h2 class="abs sec-title" style="top:1357px">Our <span class="accent">Products</span></h2>
<div class="abs sec-sub" style="top:1425px">Itaque earum rerum hic tenetur a sapiente delectus, ut aut reiciendis voluptatibus maiores alias consequatur aut perferendis doloribus asperiores repellat.</div>
<svg class="abs arrow" style="left:38px;top:1718px" viewBox="0 0 34 34"><path d="M20 10l-7 7 7 7" fill="none" stroke="#fff" stroke-width="3"/></svg>
<svg class="abs arrow" style="left:1121px;top:1718px" viewBox="0 0 34 34"><path d="M14 10l7 7-7 7" fill="none" stroke="#fff" stroke-width="3"/></svg>

<div class="abs card" style="left:111px">
  <div class="ph" role="img" aria-label="Blue gummy cubes beside hemp leaves" style="background:linear-gradient(160deg,#6f9b3a,#a88a5c 60%,#4f7bb0)"></div>
  <h3>Cannabis Edibles</h3>
  <p>Temporibus autem quibusdam et aut officiis debitis aut rerum</p>
  <span class="buy">Buy Now</span>
</div>
<div class="abs card mid" style="left:456px">
  <div class="ph" role="img" aria-label="Bottles of hemp oil with a hemp leaf" style="background:linear-gradient(160deg,#1c1c18,#5a4a1e 55%,#3d6b2a)"></div>
  <h3>Cannabis Concentrates</h3>
  <p>Itaque earum rerum hic tenetur a delectus, ut aut reiciendis</p>
  <span class="buy">Buy Now</span>
</div>
<div class="abs card" style="left:799px">
  <div class="ph" role="img" aria-label="Close-up of dried flower buds" style="background:linear-gradient(160deg,#4a5a3a,#7d7a52 50%,#2f3a26)"></div>
  <h3>THCA Flowers</h3>
  <p>Voluptatibus maiores alias consequ atur aut perferendis doloribus</p>
  <span class="buy">Buy Now</span>
</div>

<!-- get in touch -->
<div class="abs touch" role="img" aria-label="Green background of hemp leaves"></div>
<h2 class="abs sec-title" style="top:2096px;color:#fff">Get In Touch With Us</h2>
<div class="abs touch-text" style="top:2163px">Nam libero tempore, cum soluta nobis est eligendi optio cumque nihil impedit quo minus id quod maxime placeat facere possimus, omnis voluptas assumenda est, omnis dolor repellendus. Temporibus autem quibusdam et aut officiis debitis aut rerum necessitatibus saepe eveniet ut et voluptates repudiandae sint et molestiae non recusandae.</div>
<div class="abs touch-text" style="top:2279px">Itaque earum rerum hic tenetur a sapiente delectus, ut aut reiciendis voluptatibus maiores alias consequatur aut perferendis doloribus asperiores repellat.</div>
<div class="btn" style="left:377px;top:2368px;width:272px;height:49px;background:#fff;color:var(--green);font-size:19px">Call Now: +1 555 010 2040</div>
<div class="btn" style="left:695px;top:2368px;width:125px;height:49px;border:2.5px solid #fff;color:#fff;font-size:19px">View More</div>

<!-- reviews -->
<h2 class="abs sec-title" style="top:2531px">What Customer <span class="accent">Says</span></h2>
<svg class="abs arrow" style="left:38px;top:2785px" viewBox="0 0 34 34"><path d="M20 10l-7 7 7 7" fill="none" stroke="#fff" stroke-width="3"/></svg>
<svg class="abs arrow" style="left:1121px;top:2785px" viewBox="0 0 34 34"><path d="M14 10l7 7-7 7" fill="none" stroke="#fff" stroke-width="3"/></svg>

<div class="abs review" style="left:104px;top:2620px;height:339px">
  <div class="stars">★★★★★</div>
  <p>Temporibus autem quibusdam et aut officiis debitis aut rerum neus voluptates repudae sint et molestiae saepe facere mus, onis voluptas eveniet ut et voluptates repudae sint et molestiae non lorem recusadae.</p>
  <div class="who"><div class="avatar" role="img" aria-label="Customer portrait"></div><div><b>Owen Harper</b><small>United States</small></div></div>
</div>
<div class="abs review" style="left:446px;top:2660px;height:337px;border:none;box-shadow:0 4px 16px rgba(0,0,0,.1)">
  <div class="stars">★★★★★</div>
  <p>Itaque earum rerum hic tenetur a sapiene delectus, ut aut reicieis volupatibus maiores alias voluptates repudae sint et molestiae conse uatur aut perferndis doloribus asperiores reiciendis voluptatbus repellat</p>
  <div class="who"><div class="avatar" role="img" aria-label="Customer portrait"></div><div><b>Lena Brooks</b><small>United States</small></div></div>
</div>
<div class="abs review" style="left:785px;top:2620px;height:339px">
  <div class="stars">★★★★★</div>
  <p>At vero eos et accusamus et iusto odio dignissimos ducimus qui blaiis volupta molestiaepraesentium volupttum dae sint et molestia edeleniti atque coupti quos dolores et quas occaecati cupie non provident</p>
  <div class="who"><div class="avatar" role="img" aria-label="Customer portrait"></div><div><b>Marcus Reed</b><small>United States</small></div></div>
</div>

<!-- contact -->
<div class="abs contact"></div>
<h2 class="abs sec-title" style="top:3136px">Contact <span class="accent">Us</span></h2>
<div class="abs field" style="top:3215px">Name</div>
<div class="abs field" style="top:3278px">Your Phone</div>
<div class="abs field" style="top:3342px">Your Email</div>
<div class="btn btn-grad" style="left:113px;top:3406px;width:332px;height:48px;font-size:18px">SUBMIT</div>
<div class="abs field" style="left:464px;top:3215px;width:315px;height:239px">Message</div>

<div class="abs info-ic" style="top:3217px"><svg width="62" height="62" viewBox="0 0 62 62"><path d="M31 18a9 9 0 0 0-9 9c0 7 9 17 9 17s9-10 9-17a9 9 0 0 0-9-9z" fill="#fff"/><circle cx="31" cy="27" r="3.5" fill="#4c8432"/></svg></div>
<div class="abs info-txt" style="top:3207px"><b>LOCATION</b><br>Sunnyfield Hemp<br>United States</div>
<div class="abs info-ic" style="top:3310px"><svg width="62" height="62" viewBox="0 0 62 62"><path d="M23 20l5-1 3 7-3 2a14 14 0 0 0 6 6l2-3 7 3-1 5c-12 1-20-7-19-19z" fill="#fff"/></svg></div>
<div class="abs info-txt" style="top:3309px"><b>PHONE NUMBER</b><br>+1 555 010 2040</div>
<div class="abs info-ic" style="top:3389px"><svg width="62" height="62" viewBox="0 0 62 62"><rect x="20" y="23" width="22" height="16" fill="#fff"/><path d="M20 23l11 9 11-9" fill="none" stroke="#4c8432" stroke-width="2"/></svg></div>
<div class="abs info-txt" style="top:3389px"><b>EMAIL ADDRESS</b><br>info@sunnyfieldhemp.com</div>

<!-- footer -->
<footer class="abs footer">
  <div class="abs f-title" style="left:110px;top:90px">Contact Us</div>
  <div class="abs f-ic" style="top:126px"></div>
  <div class="abs" style="left:154px;top:124px;font-size:14.5px;line-height:28px">Sunnyfield Hemp<br>United States</div>
  <div class="abs f-ic" style="top:186px"></div>
  <div class="abs" style="left:154px;top:193px;font-size:14.5px">+1 555 010 2040</div>
  <div class="abs f-ic" style="top:238px"></div>
  <div class="abs" style="left:154px;top:245px;font-size:14.5px">info@sunnyfieldhemp.com</div>

  <div class="abs f-title" style="left:421px">Quick Links</div>
  <ul class="abs f-list" style="left:421px"><li>Home</li><li>About</li><li>Services</li><li>Testimonials</li><li>Contact Us</li></ul>

  <div class="abs f-title" style="left:652px">Help Links</div>
  <ul class="abs f-list" style="left:652px;top:122px"><li>FAQ</li><li>Terms of use</li><li>Privacy Policy</li><li>Support Links</li><li>Conditions</li></ul>

  <div class="abs" style="left:858px;top:90px;width:226px;text-align:center">
    <div style="width:40px;height:40px;border-radius:50%;background:#fff;margin:0 auto"></div>
    <div style="font-family:'Baloo 2',sans-serif;font-weight:700;font-size:36px;line-height:1.4">Sunnyfield</div>
  </div>
  <div class="abs f-social" style="left:867px"></div>
  <div class="abs f-social" style="left:925px"></div>
  <div class="abs f-social" style="left:983px"></div>
  <div class="abs f-social" style="left:1041px"></div>

  <div class="abs" style="left:110px;top:330px;width:980px;height:1px;background:rgba(255,255,255,.35)"></div>
  <div class="abs" style="left:0;top:358px;width:1200px;text-align:center;font-size:14.5px">Copyrights@2023.Sunnyfield Hemp.All Rights Reserved</div>
</footer>

</body>
</html>
```